PAX

We need to design a power point presentation that can englobe all our company products.

This presentation has to have all the required to be used as template for future presentations.

We focus on prodcut developing for supermarkets, ( we help them with their own brand products ex. Sunny Harvest, TK, etc.)
Also we are on the marine industry, we develop ships and oil rigs for the Oil and deep water market.

Target Market(s)

Oil Companies
Supermarket companies
Retail Companies

Industry/Entity Type

It Company

Requirements
Must have
• Our Logo and company colors
Nice to have
• Something describing globalization.
Should not have
• Orange color

```html
<!DOCTYPE html>
<html lang="en">
<head>
<meta charset="utf-8">
<title>PAX – Presentation Title</title>
<link rel="stylesheet" href="https://fonts.googleapis.com/css2?family=Open+Sans:wght@300;400&display=swap">
<style>
  :root {
    --sky-light: #7fe0ff;
    --sky: #4fcfff;
    --sky-deep: #1fb8f5;
    --band-blue: #05b4f5;
    --band-pale: #8fe3ff;
    --band-navy: #3d4a9a;
    --paper: #ffffff;
    --text-light: #ffffff;
    --text-muted: #1f5f86;
    --brand-green: #8cc63f;
  }
  * { margin: 0; padding: 0; box-sizing: border-box; }
  html, body { width: 1200px; height: 900px; overflow: hidden; }
  body { font-family: "Open Sans", Arial, sans-serif; background: var(--paper); }
  .slide { position: relative; width: 1200px; height: 900px; overflow: hidden; }
  .slide-backdrop { position: absolute; inset: 0; width: 1200px; height: 900px; }
  .title-block { position: absolute; left: 68px; top: 94px; color: var(--text-light); font-weight: 300; }
  .title-kicker { font-size: 50px; line-height: 60px; letter-spacing: 0.5px; }
  .title-main { font-size: 72px; line-height: 84px; letter-spacing: 1px; }
  .presenter { position: absolute; left: 74px; top: 750px; color: var(--text-light); font-size: 32px; font-weight: 400; }
  .slide-footer { position: absolute; left: 71px; top: 812px; color: var(--text-muted); font-size: 17px; font-weight: 400; word-spacing: 2px; }
  .brand-mark { position: absolute; left: 990px; top: 650px; width: 140px; display: flex; flex-direction: column; align-items: center; gap: 14px; }
  .brand-dot { width: 120px; height: 120px; border-radius: 50%; background: var(--brand-green); }
  .brand-name { font-size: 52px; font-weight: 400; color: var(--band-navy); letter-spacing: 4px; line-height: 1; }
</style>
</head>
<body>
  <main class="slide">
    <svg class="slide-backdrop" viewBox="0 0 1200 900" aria-hidden="true">
      <defs>
        <linearGradient id="sky-wash" x1="0" y1="0" x2="1" y2="1">
          <stop offset="0" stop-color="var(--sky-light)"/>
          <stop offset="0.35" stop-color="var(--sky)"/>
          <stop offset="1" stop-color="var(--sky-deep)"/>
        </linearGradient>
      </defs>
      <rect class="sky" width="1200" height="900" fill="url(#sky-wash)"/>
      <polygon class="sweep-soft" points="1200,368 0,900 360,900" fill="#2ec3fb" opacity="0.6"/>
      <polygon class="sweep-blue" points="1200,370 360,900 520,900" fill="var(--band-blue)"/>
      <polygon class="sweep-pale" points="1200,374 520,900 578,900" fill="var(--band-pale)"/>
      <polygon class="sweep-navy" points="1200,378 578,900 612,900" fill="var(--band-navy)"/>
      <polygon class="paper-corner" points="1200,384 612,900 1200,900" fill="var(--paper)"/>
    </svg>

    <header class="title-block">
      <p class="title-kicker">PRESENTATION TITLE:</p>
      <h1 class="title-main" style="font-weight:300">LOREM IPSUM IST EIN</h1>
    </header>

    <p class="presenter">John Doe, 12 Janu 2014</p>
    <p class="slide-footer">Public &nbsp;|&nbsp; ©Meridian Logistics PAX &nbsp;|&nbsp; 2014.01.12</p>

    <div class="brand-mark">
      <span class="brand-dot"></span>
      <span class="brand-name">PAX</span>
    </div>
  </main>
</body>
</html>
```